WordPress Site That Reviews Footwear

We need a wordpress web design for an affiliate site called PaceKite. We review and do roundups on footwear products. The final design should be clean and mobile friendly. The site should be built with Gutenberg page builder. We like the design of https://lunavessel.com/.
Updates

Need extra days to review

Target Market(s)

USA

Industry/Entity Type

Footwear

Logo Text

PaceKite

Number of Pages Required

4 page

Font styles to use
Serif
Sans Serif

Requirements
Must have
• Wordpress site
Blog post
Page
Categories
Homepage

```html
<!DOCTYPE html>
<html lang="en">
<head>
<meta charset="utf-8">
<title>PaceKite — Footwear Reviews</title>
<link rel="stylesheet" href="https://fonts.googleapis.com/css2?family=Libre+Baskerville:wght@400;700&family=Lato:wght@400;700&family=Tinos:wght@400;700&display=swap">
<style>
:root{
  --ink:#1d1b24;
  --muted:#3b3b45;
  --hero-bg:#e6e8ef;
  --welcome-bg:#eceef2;
  --white:#ffffff;
  --slate:#416475;
  --slate-light:#dce2e8;
  --gold:#efae0b;
  --featured-bg:#e4e8ec;
  --footer-bg:#dde2e7;
  --meta:#3f6274;
  --line:#c8ced5;
  --shape:#f8f8f9;
}
*{box-sizing:border-box;margin:0;padding:0}
html,body{width:1200px;height:2430px;overflow:hidden}
body{font-family:"Tinos",serif;color:var(--ink);background:var(--white);position:relative}
.abs{position:absolute}

/* header */
.site-header{position:absolute;top:0;left:0;width:1200px;height:74px;background:var(--white);border-bottom:1px solid #eceef2}
.nav-link{position:absolute;top:32px;font-size:12.5px;letter-spacing:.2px;color:var(--ink)}
.nav-link .caret{display:inline-block;width:5px;height:5px;border-right:1.3px solid var(--ink);border-bottom:1.3px solid var(--ink);transform:rotate(45deg);margin:0 0 2px 4px}
.brand{position:absolute;left:0;width:1200px;top:14px;text-align:center;font-family:"Libre Baskerville",serif;font-size:31px;letter-spacing:.5px;color:var(--ink)}
.social-sq{position:absolute;top:30px;width:16px;height:16px;border-radius:3px;background:var(--ink)}

/* hero */
.hero{position:absolute;top:75px;left:0;width:1200px;height:489px;background:linear-gradient(180deg,#e3e6ee 0%,#eef0f4 80%,#f3f4f6 100%)}
.hero-glow{position:absolute;left:10px;top:60px;width:520px;height:300px;border-radius:50%;background:radial-gradient(ellipse at center,rgba(205,208,220,.8),rgba(226,229,237,0) 70%)}
.hero-title{position:absolute;left:107px;top:108px;font-family:"Libre Baskerville",serif;font-weight:400;font-size:70px;color:var(--ink);letter-spacing:-1px}
.hero-text{position:absolute;left:112px;top:197px;width:370px;font-family:"Lato",sans-serif;font-size:13px;line-height:26px;color:var(--ink)}
.hero-cta{position:absolute;left:111px;top:270px;font-size:13.5px;letter-spacing:2px;color:var(--ink)}
.hero-cta .arrow{color:var(--gold);margin-left:8px;font-size:16px}
.cat-card{position:absolute;width:172px;height:131px;background:var(--white);border:1px solid #e2e4ea;border-radius:6px;text-align:center}
.cat-card svg{position:absolute;left:56px;top:20px}
.cat-card .label{position:absolute;left:0;right:0;top:78px;font-size:21px;color:var(--ink)}

/* welcome */
.welcome{position:absolute;top:564px;left:0;width:1200px;height:287px;background:var(--welcome-bg);overflow:hidden}
.welcome h2{position:absolute;left:0;width:1200px;top:64px;text-align:center;font-family:"Libre Baskerville",serif;font-weight:400;font-size:33px;color:var(--ink)}
.welcome p{position:absolute;left:230px;width:740px;top:118px;text-align:center;font-family:"Lato",sans-serif;font-size:13.5px;line-height:27px;color:var(--ink)}

/* features */
.features{position:absolute;top:851px;left:0;width:1200px;height:607px;background:var(--slate-light)}
.features-panel{position:absolute;left:0;top:0;width:781px;height:607px;background:var(--slate);border-radius:0 6px 6px 0}
.feature{position:absolute;width:280px;color:var(--white)}
.feature h3{font-family:"Libre Baskerville",serif;font-weight:400;font-size:29px;margin-bottom:10px}
.feature p{font-size:15.5px;line-height:23px;color:#eef2f5}
.btn-pill{position:absolute;width:150px;height:49px;border-radius:25px;background:var(--gold);color:var(--ink);font-size:14px;line-height:49px;text-align:center}
.feature-photo{position:absolute;left:704px;top:143px;width:384px;height:321px;border-radius:6px;background:linear-gradient(120deg,#c98a5c 0%,#d99c6c 40%,#7b8a6a 70%,#c7d2cf 100%)}

/* featured products */
.featured{position:absolute;top:1458px;left:0;width:1200px;height:662px;background:var(--featured-bg)}
.featured h2{position:absolute;left:0;width:1200px;top:66px;text-align:center;font-family:"Libre Baskerville",serif;font-weight:400;font-size:34px}
.featured .intro{position:absolute;left:200px;width:800px;top:118px;text-align:center;font-size:15.5px;line-height:29px}
.product{position:absolute;top:232px;width:307px}
.product .thumb{width:307px;height:189px;border-radius:6px}
.product .meta{margin-top:21px;font-size:12px;letter-spacing:.4px;color:var(--meta)}
.product .meta .dot{display:inline-block;width:8px;height:8px;background:var(--meta);border-radius:1px;margin:0 5px 0 3px}
.product h4{margin-top:10px;font-family:"Libre Baskerville",serif;font-weight:400;font-size:18px;line-height:27px;color:var(--ink)}
.product .more{margin-top:20px;font-size:13px;color:var(--ink)}
.carousel-arrow{position:absolute;top:320px}

/* footer */
.site-footer{position:absolute;top:2120px;left:0;width:1200px;height:310px;background:var(--footer-bg)}
.footer-brand{position:absolute;left:109px;top:62px;font-family:"Libre Baskerville",serif;font-size:38px;color:var(--ink)}
.footer-about{position:absolute;left:111px;top:121px;width:240px;font-size:11px;line-height:21.5px}
.footer-col h5{font-family:"Libre Baskerville",serif;font-weight:400;font-size:16px;margin-bottom:18px}
.footer-col{position:absolute;top:64px;font-size:12px}
.footer-col .row{display:flex;gap:7px;line-height:20px}
.footer-col ul{list-style:none}
.footer-col li{line-height:30px}
.newsletter-input{position:absolute;left:772px;top:104px;width:204px;height:47px;background:var(--white);border:1px solid #d9dde2;font-family:"Lato",sans-serif;font-size:12px;color:#555;padding:16px 20px}
.newsletter-btn{position:absolute;left:976px;top:104px;width:112px;height:47px;background:var(--gold);font-size:16px;font-weight:700;line-height:47px;text-align:center;letter-spacing:.5px}
.social-circle{position:absolute;top:171px;width:38px;height:38px;border-radius:50%;background:var(--white);border:1px solid #c9ced4}
.footer-rule{position:absolute;left:111px;top:247px;width:977px;height:1px;background:var(--line)}
.copyright{position:absolute;left:0;width:1200px;top:270px;text-align:center;font-size:12px}
</style>
</head>
<body>

<header class="site-header">
  <span class="nav-link" style="left:112px">PRODUCTS<span class="caret"></span></span>
  <span class="nav-link" style="left:209px">FOOTWEAR<span class="caret"></span></span>
  <span class="nav-link" style="left:317px">CONCERNS<span class="caret"></span></span>
  <span class="nav-link" style="left:419px">REVIEWS<span class="caret"></span></span>
  <div class="brand">PaceKite</div>
  <span class="nav-link" style="left:828px">ABOUT</span>
  <span class="nav-link" style="left:893px">CONTACT</span>
  <span class="social-sq" style="left:1002px"></span>
  <span class="social-sq" style="left:1037px"></span>
  <span class="social-sq" style="left:1071px"></span>
</header>

<section class="hero">
  <div class="hero-glow"></div>
  <h1 class="hero-title">PaceKite</h1>
  <p class="hero-text">Temporibus autem quibusdam et aut officiis debitis aut rerum eveniet ut et voluptates repudiandae sint et molestiae</p>
  <div class="hero-cta">CHECK OUT A FEW OF OUR FAVORITES<span class="arrow">&#8594;</span></div>

  <div class="cat-card" style="left:538px;top:95px">
    <svg width="60" height="40" viewBox="0 0 60 40" fill="none" stroke="#1d1b24" stroke-width="1.8"><path d="M4 30 V14 l8 -3 l6 4 l14 2 l18 6 q6 2 6 7 v4 H4z"/><path d="M4 30 H56"/></svg>
    <div class="label">Esse Cillum</div>
  </div>
  <div class="cat-card" style="left:726px;top:95px">
    <svg width="60" height="40" viewBox="0 0 60 40" fill="none" stroke="#1d1b24" stroke-width="1.8"><path d="M6 36 V8 q2 -4 6 0 q10 14 22 18 q10 2 18 4 q4 2 0 4 H18 q-4 -10 -8 -10 v12z"/></svg>
    <div class="label">Necessitatibus</div>
  </div>
  <div class="cat-card" style="left:914px;top:95px">
    <svg width="60" height="44" viewBox="0 0 60 44" fill="none" stroke="#1d1b24" stroke-width="1.8"><rect x="12" y="2" width="14" height="40" rx="7"/><rect x="34" y="2" width="14" height="40" rx="7"/></svg>
    <div class="label">Cumque Nihi</div>
  </div>
  <div class="cat-card" style="left:538px;top:258px">
    <svg width="60" height="40" viewBox="0 0 60 40" fill="none" stroke="#1d1b24" stroke-width="1.8"><path d="M4 30 V14 l8 -3 l6 4 l14 2 l18 6 q6 2 6 7 v4 H4z"/><path d="M4 30 H56"/></svg>
    <div class="label">Esse Cillum</div>
  </div>
  <div class="cat-card" style="left:726px;top:258px">
    <svg width="60" height="40" viewBox="0 0 60 40" fill="none" stroke="#1d1b24" stroke-width="1.8"><path d="M6 36 V8 q2 -4 6 0 q10 14 22 18 q10 2 18 4 q4 2 0 4 H18 q-4 -10 -8 -10 v12z"/></svg>
    <div class="label">Necessitatibus</div>
  </div>
  <div class="cat-card" style="left:914px;top:258px">
    <svg width="60" height="44" viewBox="0 0 60 44" fill="none" stroke="#1d1b24" stroke-width="1.8"><rect x="12" y="2" width="14" height="40" rx="7"/><rect x="34" y="2" width="14" height="40" rx="7"/></svg>
    <div class="label">Cumque Nihi</div>
  </div>
</section>

<section class="welcome">
  <svg class="abs" style="left:0;top:0" width="1200" height="287" viewBox="0 0 1200 287">
    <path d="M500 287 C600 120 650 0 740 0 C830 0 940 80 1165 287Z" fill="var(--shape)"/>
    <path d="M15 287 C60 230 120 222 160 230 C200 240 230 260 260 287Z" fill="var(--shape)"/>
    <circle cx="347" cy="147" r="50" fill="var(--shape)"/>
  </svg>
  <h2>Welcome to PaceKite</h2>
  <p>Temporibus autem quibusdam et aut officiis debitis aut rerum necessitatibus saepe eveniet ut et voluptates repudiandae sint et molestiae non recusandae.</p>
</section>

<section class="features">
  <div class="features-panel"></div>
  <div class="feature" style="left:111px;top:84px"><h3>Consectetur</h3><p>Lorem ipsum dolor sit amet, consectetur adipiscing elit, sed do eiusmod tempor incididunt ut labore et dolore magna.</p></div>
  <div class="btn-pill" style="left:111px;top:222px">LEARN MORE</div>
  <div class="feature" style="left:420px;top:84px"><h3>Dolorem Ipsum</h3><p>Lorem ipsum dolor sit amet, consectetur adipiscing elit, sed do eiusmod tempor incididunt ut labore et dolore magna.</p></div>
  <div class="btn-pill" style="left:420px;top:222px">LEARN MORE</div>
  <div class="feature" style="left:111px;top:315px"><h3>Magni Dolores</h3><p>Lorem ipsum dolor sit amet, consectetur adipiscing elit, sed do eiusmod tempor incididunt ut labore et dolore magna.</p></div>
  <div class="btn-pill" style="left:111px;top:454px">LEARN MORE</div>
  <div class="feature" style="left:420px;top:315px"><h3>Exercitationem</h3><p>Lorem ipsum dolor sit amet, consectetur adipiscing elit, sed do eiusmod tempor incididunt ut labore et dolore magna.</p></div>
  <div class="btn-pill" style="left:420px;top:454px">LEARN MORE</div>
  <div class="feature-photo" role="img" aria-label="Photo of a parent helping a child try on shoes in a store"></div>
</section>

<section class="featured">
  <h2>Featured Products</h2>
  <p class="intro">Sed ut perspiciatis unde omnis iste natus error sit voluptatem accusantium doloremque laudantium, totam rem aperiam, eaque ipsa quae ab illo inventore veritatis et quasi architecto beatae vitae dicta sunt explicabo.</p>

  <svg class="carousel-arrow" style="left:60px" width="26" height="40" viewBox="0 0 26 40"><path d="M22 3 L5 20 L22 37" fill="none" stroke="#c3c9d2" stroke-width="6"/></svg>
  <svg class="carousel-arrow" style="left:1113px" width="26" height="40" viewBox="0 0 26 40"><path d="M4 3 L21 20 L4 37" fill="none" stroke="#c3c9d2" stroke-width="6"/></svg>

  <article class="product" style="left:111px">
    <div class="thumb" role="img" aria-label="Photo of red baby sneakers on a white rug" style="background:linear-gradient(135deg,#d9d6d0,#c96a72 50%,#e4e1dc)"></div>
    <div class="meta">PRODUCT REVIEWS<span class="dot"></span>2 MONTHS AGO</div>
    <h4>Excepteur sint occaecat cupidatat non proident</h4>
    <div class="more">READ MORE &#10230;</div>
  </article>
  <article class="product" style="left:446px">
    <div class="thumb" role="img" aria-label="Photo of several pairs of kids' sneakers on a light floor" style="background:linear-gradient(135deg,#e6e4dc,#c9c7a8 45%,#8e98a0 70%,#e2e0d8)"></div>
    <div class="meta">PRODUCT REVIEWS<span class="dot"></span>6 MONTHS AGO</div>
    <h4>Temporibus autem quibusdam et aut officiis debitis</h4>
    <div class="more">READ MORE &#10230;</div>
  </article>
  <article class="product" style="left:781px">
    <div class="thumb" role="img" aria-label="Photo of white kids' shoes against a blue wall" style="background:linear-gradient(180deg,#8fd0ef 0%,#7cc2e6 62%,#b6c3cc 75%,#9aa8b3 100%)"></div>
    <div class="meta">PRODUCT REVIEWS<span class="dot"></span>5 MONTHS AGO</div>
    <h4>Et harum quidem rerum facilis est et expedita distinctio</h4>
    <div class="more">READ MORE &#10230;</div>
  </article>
</section>

<footer class="site-footer">
  <div class="footer-brand">PaceKite</div>
  <p class="footer-about">At vero eos et accusamus et iusto odio dignissimos ducimus qui blanditiis praesentium voluptatum deleniti atque corrupti quos dolores</p>

  <div class="footer-col" style="left:396px">
    <h5>Where to Find us</h5>
    <div class="row">
      <svg width="9" height="13" viewBox="0 0 9 13" style="margin-top:4px"><path d="M4.5 0 A4.5 4.5 0 0 1 9 4.5 C9 8 4.5 13 4.5 13 C4.5 13 0 8 0 4.5 A4.5 4.5 0 0 1 4.5 0Z" fill="#1d1b24"/><circle cx="4.5" cy="4.5" r="1.7" fill="#dde2e7"/></svg>
      <div>48 Alder Row,<br>Westbrook, USA<br>60412</div>
    </div>
    <div class="row" style="margin-top:28px">
      <svg width="11" height="11" viewBox="0 0 24 24" style="margin-top:5px"><path d="M6.6 10.8a15 15 0 0 0 6.6 6.6l2.2-2.2a1 1 0 0 1 1-.25 11.4 11.4 0 0 0 3.6.57 1 1 0 0 1 1 1V20a1 1 0 0 1-1 1A17 17 0 0 1 3 4a1 1 0 0 1 1-1h3.5a1 1 0 0 1 1 1c0 1.25.2 2.45.57 3.57a1 1 0 0 1-.25 1z" fill="#1d1b24"/></svg>
      <div>(555) 014-2287</div>
    </div>
  </div>

  <div class="footer-col" style="left:611px">
    <h5>Information</h5>
    <ul><li>Shop</li><li>Blog</li><li>About</li><li>Contact Us</li></ul>
  </div>

  <div class="footer-col" style="left:769px"><h5>Join Our Newsletter</h5></div>
  <div class="newsletter-input">Email</div>
  <div class="newsletter-btn">SUBMIT</div>
  <span class="social-circle" style="left:768px"></span>
  <span class="social-circle" style="left:815px"></span>
  <span class="social-circle" style="left:862px"></span>
  <span class="social-circle" style="left:909px"></span>

  <div class="footer-rule"></div>
  <p class="copyright">Copyrights &copy; 2021 PaceKite. All rights reserved.</p>
</footer>

</body>
</html>
```